Quillfield Climate Business Card Design

Design new, 2 sides, business cards for a residential and light commercial heating, air conditioning contractor.

Target Market(s)

Homeowners, small businesses

Industry/Entity Type

Business

Contact Information for Business Card

Dominic Westerhall
Phone - 862-415-2736
Email
Address - PO box 518
Brightwater NJ 07912
Website - www.HarborBreezeLLC.example

Requirements
Must have
• logo, company colors, standard size with no die cut, so I can use nova stamp

```html
<!DOCTYPE html>
<html lang="en">
<head>
<meta charset="utf-8">
<title>Quillfield Climate Business Card</title>
<link rel="stylesheet" href="https://fonts.googleapis.com/css2?family=Open+Sans:wght@400;600;700&display=swap">
<style>
  :root {
    --maroon: #9c1f36;
    --orange: #f39a1c;
    --cream: #fbe9c9;
    --ink: #4a4a4a;
    --paper: #ffffff;
    --backdrop: #b9b9b9;
  }
  * { margin: 0; padding: 0; box-sizing: border-box; }
  html, body {
    width: 1200px; height: 950px; overflow: hidden;
    background: var(--backdrop);
    font-family: "Open Sans", Arial, sans-serif;
  }
  .sheet {
    width: 1200px; height: 950px;
    display: flex; flex-direction: column; align-items: center; justify-content: center;
    gap: 34px;
  }
  .card {
    position: relative;
    width: 760px; height: 434px;
    overflow: hidden;
  }
  /* Front */
  .card--front {
    background: var(--maroon);
    color: var(--paper);
    display: flex; flex-direction: column; align-items: center; justify-content: center;
  }
  .brand {
    display: flex; align-items: center; gap: 14px;
    font-weight: 700;
    letter-spacing: 1px;
    text-transform: uppercase;
    white-space: nowrap;
  }
  .brand__dot { width: 26px; height: 26px; border-radius: 50%; flex: none; }
  .card--front .brand { font-size: 46px; color: var(--cream); }
  .card--front .brand__dot { background: var(--orange); }
  .tagline {
    margin-top: 46px;
    text-align: center;
    font-size: 19px; line-height: 1.4;
    color: var(--cream);
  }
  /* Back */
  .card--back { background: var(--paper); }
  .card__shapes { position: absolute; inset: 0; }
  .card--back .brand {
    position: absolute; top: 66px; right: 52px;
    font-size: 34px; color: var(--maroon);
  }
  .card--back .brand__dot { background: var(--orange); width: 20px; height: 20px; }
  .contact {
    position: absolute; left: 46px; bottom: 34px;
    color: var(--ink);
  }
  .contact__name {
    font-size: 28px; font-weight: 600; color: var(--maroon);
    text-transform: uppercase; letter-spacing: .5px;
  }
  .contact__role { font-size: 17px; color: var(--orange); margin-bottom: 16px; }
  .contact__line { font-size: 17px; line-height: 1.55; }
  .contact__label { font-weight: 700; color: var(--maroon); }
</style>
</head>
<body>
<main class="sheet">
  <section class="card card--front">
    <div class="brand"><span class="brand__dot"></span>Quillfield Climate</div>
    <p class="tagline">Residential &amp; light commercial heating<br>Air conditioning contractor</p>
  </section>

  <section class="card card--back">
    <svg class="card__shapes" viewBox="0 0 760 434" width="760" height="434" aria-hidden="true">
      <path d="M0,0 L130,0 C80,12 64,60 58,115 C52,160 30,178 0,185 Z" fill="var(--maroon)"/>
      <path d="M760,150 C700,178 684,250 694,315 C704,380 680,420 630,434 L760,434 Z" fill="var(--orange)"/>
    </svg>
    <div class="brand"><span class="brand__dot"></span>Quillfield Climate</div>
    <div class="contact">
      <h1 class="contact__name">Dominic Westerhall</h1>
      <p class="contact__role">CEO/Founder</p>
      <p class="contact__line"><span class="contact__label">P:</span> 862 415 2736</p>
      <p class="contact__line"><span class="contact__label">M:</span> 862 415 2790 | <span class="contact__label">F:</span> 862 415 2741</p>
      <p class="contact__line"><span class="contact__label">E:</span> dominic@quillfieldclimate.example</p>
      <p class="contact__line"><span class="contact__label">W:</span> www.QuillfieldClimateLLC.example</p>
      <p class="contact__line">PO box 518, Brightwater NJ 07912</p>
    </div>
  </section>
</main>
</body>
</html>
```